IT Company requires new Business Card design.

Over the years we have had a few different business card designs. We are now due for new cards across the board for all staff. We felt this would be a good time to start fresh with a new design. Our traditional card simply had our details on the front, and a list of services on the back. We don't particularly need the list of services, we have had cards where the only thing on the rear of the card was our logo.
Feel free to be creative, we would like our tag line "Complete IT Management" to appear at some point, doesn't necessarily have to be with the logo.
I have attached samples and drafts of various previous cards we have used over the years.

```html
<!DOCTYPE html>
<html lang="en">
<head>
<meta charset="utf-8">
<title>Ridgeway Systems – Business Card</title>
<link href="https://fonts.googleapis.com/css2?family=Open+Sans:wght@400;600;700&display=swap" rel="stylesheet">
<style>
  :root {
    --slate: #5f6f7a;
    --ink: #3a3f44;
    --paper: #ffffff;
    --backdrop: #e6e7e8;
  }
  * { margin: 0; padding: 0; box-sizing: border-box; }
  html, body {
    width: 1034px; height: 1200px; overflow: hidden;
    background: var(--backdrop);
    font-family: "Open Sans", Arial, sans-serif;
    color: var(--ink);
  }
  .card {
    position: absolute; left: 74px; width: 900px; height: 515px;
    background: var(--paper);
    box-shadow: 0 2px 8px rgba(0,0,0,.18);
  }
  .card--front { top: 65px; }
  .card--back { top: 631px; }

  .name-band {
    position: absolute; top: 0; left: 0; right: 0; height: 60px;
    background: var(--slate); color: var(--paper);
    display: flex; align-items: center; justify-content: center;
    font-size: 25px;
  }
  .name-band .person { font-weight: 700; }
  .name-band .role { font-size: 21px; margin-left: 6px; }
  .rule {
    position: absolute; left: 0; right: 0; height: 2px; background: var(--slate);
  }
  .rule--top { top: 67px; }
  .rule--bottom { top: 444px; }

  .brand {
    position: absolute; top: 100px; left: 0; right: 0;
    display: flex; align-items: center; justify-content: center; gap: 22px;
    color: var(--slate); font-weight: 700;
  }
  .brand .mark { width: 60px; height: 60px; background: var(--slate); }
  .brand .wordmark { font-size: 52px; line-height: 1; letter-spacing: 1px; }

  .contact {
    position: absolute; top: 308px; left: 0; right: 0;
    text-align: center; font-size: 21px; line-height: 43px;
  }
  .contact .item { display: inline-flex; align-items: center; margin: 0 8px; }
  .contact svg { width: 20px; height: 20px; margin-right: 8px; fill: var(--ink); }

  .tagline-band {
    position: absolute; top: 453px; left: 0; right: 0; height: 62px;
    background: var(--slate); color: var(--paper);
    display: flex; align-items: center; justify-content: center;
    font-size: 23px; letter-spacing: 5px;
  }

  .back-brand {
    position: absolute; top: 150px; left: 0; right: 0;
    display: flex; align-items: center; justify-content: center; gap: 30px;
    color: var(--slate); font-weight: 700;
  }
  .back-brand .mark { width: 110px; height: 110px; background: var(--slate); }
  .back-brand .wordmark { font-size: 70px; line-height: 1.05; }
  .back-web {
    position: absolute; top: 462px; left: 0; right: 0;
    text-align: center; font-size: 27px; letter-spacing: 2px; color: var(--ink);
  }
  .back-web strong { font-weight: 600; }
</style>
</head>
<body>

<section class="card card--front">
  <header class="name-band"><span class="person">Martin Hale,</span><span class="role">Operations Manager</span></header>
  <div class="rule rule--top"></div>

  <div class="brand">
    <span class="mark"></span>
    <span class="wordmark">RIDGEWAY<br>SYSTEMS</span>
  </div>

  <div class="contact">
    <div>
      <span class="item"><svg viewBox="0 0 20 20"><path d="M5 2l3 4-2 2c1 2 3 4 5 5l2-2 4 3-2 3C9 17 3 11 2 4z"/></svg>08 9350 4418</span>
      <span class="item"><svg viewBox="0 0 20 20"><rect x="5" y="1" width="10" height="18" rx="2"/><rect x="7" y="4" width="6" height="7" fill="#fff"/></svg>0412 880 561</span>
      <span class="item"><svg viewBox="0 0 20 20"><rect x="5" y="2" width="10" height="6"/><rect x="2" y="8" width="16" height="7" rx="1"/><rect x="5" y="13" width="10" height="5"/></svg>08 9350 4418</span>
    </div>
    <div>
      <span class="item"><svg viewBox="0 0 20 20"><path d="M2 8l8-5 8 5v9H2z"/><path d="M3 9l7 5 7-5" fill="none" stroke="#fff" stroke-width="1.5"/></svg>martin@ridgewaysystems.com.au</span>
      <span class="item"><svg viewBox="0 0 20 20"><circle cx="10" cy="10" r="8"/><path d="M2 10h16M10 2c-4 4-4 12 0 16M10 2c4 4 4 12 0 16" fill="none" stroke="#fff" stroke-width="1.3"/></svg>www.ridgewaysystems.com.au</span>
    </div>
    <div>Unit 7 22 Harbour Lane, Kelmscott WA 6111</div>
  </div>

  <div class="rule rule--bottom"></div>
  <footer class="tagline-band">COMPLETE IT MANAGEMENT</footer>
</section>

<section class="card card--back">
  <div class="back-brand">
    <span class="mark"></span>
    <span class="wordmark">RIDGEWAY<br>SYSTEMS</span>
  </div>
  <div class="back-web">www.<strong>ridgewaysystems</strong>.com.au</div>
</section>

</body>
</html>
```